Design a Mobile App for Landscape Businesses

This project is to design the first three screens for a mobile app for Landscape and Lawncare businesses. This app will serve as a directory for homeowners to locate landscape and lawn care businesses and for landscape businesses and contractors to run their business. See the attached PDF for more information and example
Here is the link to the description https://lnkbrev.example/q7z3Kp

Target Market(s)

Landscape and lawn care business, gardeners, home owners

Industry/Entity Type

Landscape Gardening

Logo Text

Verdalink

Colors

Designer to choose colors to be used in the design.

```html
<!DOCTYPE html>
<html lang="en">
<head>
<meta charset="utf-8">
<title>Verdalink – Find a Gardener</title>
<link href="https://fonts.googleapis.com/css2?family=Montserrat:wght@400;500;600;700&display=swap" rel="stylesheet">
<style>
  :root {
    --bg: #eef0f2;
    --screen: #ffffff;
    --ink: #1c2433;
    --ink-soft: #5b6472;
    --accent: #22a6d6;
    --line: #e3e6ea;
    --nav-ink: #9aa1ab;
    --badge: #f26a21;
    --photo-one-a: #6e5a4e;
    --photo-one-b: #4f6a3d;
    --photo-two-a: #8fb4dc;
    --photo-two-b: #7d8a6a;
  }
  * { box-sizing: border-box; margin: 0; padding: 0; }
  html, body { width: 1200px; height: 800px; overflow: hidden; }
  body {
    background: var(--bg);
    font-family: "Montserrat", sans-serif;
    color: var(--ink);
    display: flex; align-items: center; justify-content: center;
  }
  .app-screen {
    width: 400px; height: 760px;
    background: var(--screen);
    display: flex; flex-direction: column;
    overflow: hidden;
    box-shadow: 0 10px 40px rgba(28,36,51,.12);
  }
  .status-bar {
    height: 24px; padding: 0 12px;
    display: flex; justify-content: flex-end; align-items: center; gap: 6px;
    font-size: 11px; font-weight: 600;
  }
  .status-bar svg { width: 12px; height: 12px; fill: var(--ink); }
  .search-header { border-bottom: 1px solid var(--line); }
  .header-links {
    display: flex; justify-content: flex-end; gap: 22px;
    padding: 6px 18px 8px; font-size: 13px; font-weight: 600; color: var(--accent);
  }
  .header-fields { display: grid; grid-template-columns: 1fr 1fr; }
  .field { padding: 10px 16px 14px; }
  .field + .field { border-left: 1px solid var(--line); }
  .field-row { display: flex; align-items: center; gap: 6px; }
  .field-title { font-size: 15px; font-weight: 700; }
  .field-sub { font-size: 11px; font-weight: 600; margin-top: 8px; }
  .field-value { font-size: 12px; }
  .field-value strong { font-weight: 700; }
  .icon-accent { width: 12px; height: 12px; fill: none; stroke: var(--accent); stroke-width: 2; }
  .icon-pin { fill: var(--accent); stroke: none; }
  .chevron { width: 10px; height: 10px; fill: none; stroke: var(--ink); stroke-width: 2; margin-left: auto; }
  .listing { flex: 1; overflow: hidden; }
  .card-photo {
    height: 168px; position: relative;
    display: flex; align-items: flex-end; padding: 12px;
  }
  .photo-front-garden { background: linear-gradient(160deg, var(--photo-one-a), var(--photo-one-b)); }
  .photo-bungalow { background: linear-gradient(180deg, var(--photo-two-a) 0%, #d9d6cc 55%, var(--photo-two-b) 100%); }
  .area-tags { display: flex; gap: 6px; }
  .area-tag {
    display: flex; align-items: center; gap: 4px;
    padding: 4px 10px; border: 1px solid rgba(255,255,255,.85); border-radius: 14px;
    background: rgba(28,36,51,.35);
    color: #fff; font-size: 10px; font-weight: 500;
  }
  .area-tag svg { width: 9px; height: 9px; fill: var(--accent); }
  .card-info { padding: 14px 18px 16px; }
  .card-title-row { display: flex; align-items: center; justify-content: space-between; }
  .business-name { font-size: 16px; font-weight: 700; }
  .quote-link { display: flex; align-items: center; gap: 4px; color: var(--accent); font-size: 12px; font-weight: 600; }
  .quote-link svg { width: 10px; height: 12px; fill: none; stroke: var(--accent); stroke-width: 2; }
  .business-about { font-size: 11px; line-height: 1.5; color: var(--ink-soft); margin-top: 6px; }
  .business-phone { display: flex; align-items: center; gap: 8px; margin-top: 8px; font-size: 12px; font-weight: 500; }
  .business-phone svg { width: 10px; height: 15px; fill: none; stroke: var(--accent); stroke-width: 1.6; }
  .tab-bar {
    height: 62px; border-top: 1px solid var(--line);
    display: grid; grid-template-columns: repeat(4, 1fr);
  }
  .tab {
    display: flex; flex-direction: column; align-items: center; justify-content: center; gap: 4px;
    font-size: 10px; color: var(--nav-ink); position: relative;
  }
  .tab svg { width: 20px; height: 18px; fill: none; stroke: var(--nav-ink); stroke-width: 1.5; }
  .tab.is-active { color: var(--accent); font-weight: 600; }
  .tab.is-active svg { stroke: var(--accent); }
  .tab-badge {
    position: absolute; top: 13px; left: 54px;
    width: 7px; height: 7px; border-radius: 50%; background: var(--badge);
  }
</style>
</head>
<body>
<main class="app-screen">
  <div class="status-bar">
    <svg viewBox="0 0 12 12"><path d="M6 11 0 4a9 9 0 0 1 12 0z"/></svg>
    <svg viewBox="0 0 12 12"><path d="M11 1v10H1z"/></svg>
    <svg viewBox="0 0 12 12"><rect x="3" y="1" width="6" height="10" rx="1"/></svg>
    <span>16:54</span>
  </div>

  <header class="search-header">
    <nav class="header-links"><span>Filter</span><span>Map</span></nav>
    <div class="header-fields">
      <div class="field">
        <div class="field-row">
          <span class="field-title">Find a Gardener</span>
          <svg class="chevron" viewBox="0 0 10 10"><path d="M2 3l3 3 3-3"/></svg>
        </div>
        <div class="field-row field-sub">
          <svg class="icon-accent icon-pin" viewBox="0 0 12 12"><path d="M6 0a4 4 0 0 1 4 4c0 3-4 8-4 8S2 7 2 4a4 4 0 0 1 4-4zm0 2.5a1.5 1.5 0 1 0 0 3 1.5 1.5 0 0 0 0-3z"/></svg>
          Current Location
        </div>
      </div>
      <div class="field">
        <div class="field-row field-value">
          <svg class="icon-accent" viewBox="0 0 12 12"><circle cx="6" cy="6" r="5"/><path d="M6 3v3l2 1"/></svg>
          <span>Available: <strong>Anytime</strong></span>
          <svg class="chevron" viewBox="0 0 10 10"><path d="M2 3l3 3 3-3"/></svg>
        </div>
      </div>
    </div>
  </header>

  <section class="listing">
    <article class="gardener-card">
      <div class="card-photo photo-front-garden" role="img" aria-label="Photo of a brick house with a landscaped front garden of shrubs and a small red-leaved tree">
        <div class="area-tags">
          <span class="area-tag"><svg viewBox="0 0 12 12"><path d="M6 0a4 4 0 0 1 4 4c0 3-4 8-4 8S2 7 2 4a4 4 0 0 1 4-4z"/></svg>Scarborough</span>
          <span class="area-tag"><svg viewBox="0 0 12 12"><path d="M6 0a4 4 0 0 1 4 4c0 3-4 8-4 8S2 7 2 4a4 4 0 0 1 4-4z"/></svg>Whitby</span>
          <span class="area-tag"><svg viewBox="0 0 12 12"><path d="M6 0a4 4 0 0 1 4 4c0 3-4 8-4 8S2 7 2 4a4 4 0 0 1 4-4z"/></svg>Filey</span>
        </div>
      </div>
      <div class="card-info">
        <div class="card-title-row">
          <h2 class="business-name">Hollis Gardencraft</h2>
          <span class="quote-link">Quote <svg viewBox="0 0 10 12"><path d="M3 1l5 5-5 5"/></svg></span>
        </div>
        <p class="business-about">Experienced and skilled gardener based in Scarborough. I specialise in law care, hedge…</p>
        <p class="business-phone">
          <svg viewBox="0 0 10 15"><rect x="1" y="1" width="8" height="13" rx="1.5"/><path d="M4 12h2"/></svg>
          07700 900 318
        </p>
      </div>
    </article>

    <article class="gardener-card">
      <div class="card-photo photo-bungalow" role="img" aria-label="Photo of a pale bungalow with a grey roof behind a trimmed lawn and bare trees">
        <div class="area-tags">
          <span class="area-tag"><svg viewBox="0 0 12 12"><path d="M6 0a4 4 0 0 1 4 4c0 3-4 8-4 8S2 7 2 4a4 4 0 0 1 4-4z"/></svg>Scarborough</span>
          <span class="area-tag"><svg viewBox="0 0 12 12"><path d="M6 0a4 4 0 0 1 4 4c0 3-4 8-4 8S2 7 2 4a4 4 0 0 1 4-4z"/></svg>Whitby</span>
          <span class="area-tag"><svg viewBox="0 0 12 12"><path d="M6 0a4 4 0 0 1 4 4c0 3-4 8-4 8S2 7 2 4a4 4 0 0 1 4-4z"/></svg>Filey</span>
        </div>
      </div>
    </article>
  </section>

  <nav class="tab-bar">
    <div class="tab is-active">
      <svg viewBox="0 0 20 18"><path d="M6 1a4 4 0 0 1 4 4c0 3-4 8-4 8S2 8 2 5a4 4 0 0 1 4-4z"/><path d="M14 4a4 4 0 0 1 4 4c0 3-4 8-4 8s-4-5-4-8"/></svg>
      Search
    </div>
    <div class="tab">
      <svg viewBox="0 0 20 18"><path d="M3 4h1M3 9h1M3 14h1M7 4h10M7 9h10M7 14h10"/></svg>
      Bookings
    </div>
    <div class="tab">
      <svg viewBox="0 0 20 18"><rect x="2" y="3" width="16" height="12" rx="1"/><path d="M2 4l8 6 8-6"/></svg>
      <span class="tab-badge"></span>
      Messages
    </div>
    <div class="tab">
      <svg viewBox="0 0 20 18"><circle cx="10" cy="9" r="3"/><circle cx="10" cy="9" r="7" stroke-dasharray="3 2"/></svg>
      Account
    </div>
  </nav>
</main>
</body>
</html>
```